Vantro cards

I am in the auto motive, transportation business I would like a business card that is Something cool, modern edgy, having to do with car culture. I offer towing service for high and exotic cars. I also provide towing for collisions and car accidents. I offer open and enclosed transport nationwide.

Target Market(s)

Car culture people high end auto collectors

Industry/Entity Type

Towing car carrier

Contact Information for Business Card

My company colors black yellow and silver

Font styles to use
Serif

```html
<!DOCTYPE html>
<html lang="en">
<head>
<meta charset="utf-8">
<title>Vantro Business Cards</title>
<link href="https://fonts.googleapis.com/css2?family=Poppins:wght@400;600;800&display=swap" rel="stylesheet">
<style>
  :root {
    --backdrop: #e4e4e4;
    --card-white: #ffffff;
    --brand-yellow: #fbe05f;
    --ink: #111111;
    --muted: #8a8a8a;
    --rule: #555555;
  }
  * { box-sizing: border-box; margin: 0; padding: 0; }
  html, body {
    width: 1200px; height: 930px; overflow: hidden;
    background: var(--backdrop);
    font-family: "Poppins", sans-serif;
    color: var(--ink);
  }
  .sheet {
    position: relative; width: 1200px; height: 930px;
    display: flex; align-items: center; justify-content: center; gap: 40px;
  }
  .card {
    width: 540px; height: 310px;
    box-shadow: 0 6px 18px rgba(0,0,0,0.12);
    position: relative;
  }
  .card--front { background: var(--card-white); }
  .card--back {
    background: var(--brand-yellow);
    display: flex; align-items: center; justify-content: center;
  }
  .wordmark {
    display: flex; align-items: center; gap: 10px;
    font-family: "Poppins", sans-serif; font-weight: 800;
    text-transform: uppercase; color: var(--ink); letter-spacing: 2px;
  }
  .wordmark__square { width: 14px; height: 14px; background: var(--ink); }
  .card--front .wordmark {
    position: absolute; top: 48px; left: 0; right: 0;
    justify-content: center; font-size: 34px;
  }
  .card--front .wordmark__square { background: var(--brand-yellow); }
  .card--back .wordmark { font-size: 58px; }
  .card--back .wordmark__square { width: 22px; height: 22px; }
  .holder {
    position: absolute; top: 118px; left: 0; right: 0; text-align: center;
  }
  .holder__name { font-weight: 600; font-size: 17px; letter-spacing: 1.5px; text-transform: uppercase; }
  .holder__title { font-weight: 400; font-size: 11px; letter-spacing: 1.5px; color: var(--muted); text-transform: uppercase; }
  .details {
    position: absolute; top: 178px; left: 0; right: 0;
    display: flex; justify-content: center; align-items: stretch; gap: 16px;
  }
  .details__address {
    text-align: right; font-size: 13px; line-height: 1.45;
  }
  .details__rule { width: 1px; background: var(--rule); }
  .details__contact { list-style: none; font-size: 14px; line-height: 1.45; }
  .details__contact li { display: flex; align-items: center; gap: 7px; }
  .details__contact svg { width: 12px; height: 12px; flex: none; }
</style>
</head>
<body>
<main class="sheet">
  <section class="card card--front" aria-label="Card front">
    <div class="wordmark"><span class="wordmark__square"></span>Vantro</div>
    <div class="holder">
      <p class="holder__name">Marcus Hale</p>
      <p class="holder__title">Managing Director</p>
    </div>
    <div class="details">
      <p class="details__address">421, Address line<br>goes here<br>45452, Country Name</p>
      <span class="details__rule"></span>
      <ul class="details__contact">
        <li>
          <svg viewBox="0 0 24 24" aria-hidden="true"><path fill="#111" d="M6.6 10.8a15.1 15.1 0 0 0 6.6 6.6l2.2-2.2a1 1 0 0 1 1-.25 11.4 11.4 0 0 0 3.6.57 1 1 0 0 1 1 1V20a1 1 0 0 1-1 1A17 17 0 0 1 3 4a1 1 0 0 1 1-1h3.5a1 1 0 0 1 1 1c0 1.25.2 2.46.57 3.6a1 1 0 0 1-.25 1z"/></svg>
          044-555 018 274
        </li>
        <li>
          <svg viewBox="0 0 24 24" aria-hidden="true"><rect x="2" y="5" width="20" height="14" fill="#111"/><path d="M2 5l10 8 10-8" stroke="#fff" stroke-width="1.6" fill="none"/></svg>
          info@vantrotow.com
        </li>
        <li>
          <svg viewBox="0 0 24 24" aria-hidden="true"><circle cx="12" cy="12" r="10" fill="#111"/><path d="M2 12h20M12 2c3 3 3 17 0 20M12 2c-3 3-3 17 0 20" stroke="#fff" stroke-width="1.3" fill="none"/></svg>
          www.vantrotow.com
        </li>
      </ul>
    </div>
  </section>
  <section class="card card--back" aria-label="Card back">
    <div class="wordmark"><span class="wordmark__square"></span>Vantro</div>
  </section>
</main>
</body>
</html>
```